HearthMile business card and stationary design

We are looking for a simple yet elegant design for our mortgage company business card and stationary.

The card should include:
Name (Marcus Pell)
Title (CEO)
Phone Number (732-555-0182)
Address (48 Birchwell Court, Suite 314, Marlow Springs, NJ 07741)
Email (email@hearthmile.example)
"NMLS" i.e. (NMLS 61947)
"Company NMLS" (Company NMLS 274615)

Contact Information for Business Card

See above

```html
<!DOCTYPE html>
<html lang="en">
<head>
<meta charset="utf-8">
<title>HearthMile Business Card</title>
<link href="https://fonts.googleapis.com/css2?family=Montserrat:wght@400;500;600&display=swap" rel="stylesheet">
<style>
  :root {
    --backdrop: #2a2a2c;
    --card: #1c1c1e;
    --accent: #1ea0e0;
    --text: #f2f2f2;
    --muted: #d6d6d6;
    --emboss: #9a9a9c;
  }
  * { margin: 0; padding: 0; box-sizing: border-box; }
  html, body {
    width: 1200px; height: 900px; overflow: hidden;
    background: var(--backdrop);
    font-family: "Montserrat", sans-serif;
  }
  .sheet {
    width: 1200px; height: 900px;
    display: flex; flex-direction: column; align-items: center; justify-content: center; gap: 50px;
  }
  .card {
    position: relative;
    width: 560px; height: 320px;
    background: var(--card);
    overflow: hidden;
    box-shadow: 0 10px 30px rgba(0,0,0,.45);
  }
  .card__band {
    position: absolute; left: 0; right: 0; bottom: 0; height: 7px;
    background: var(--accent);
  }
  /* front */
  .brand-name {
    position: absolute; left: 40px; top: 44px;
    font-size: 40px; font-weight: 500; letter-spacing: .5px;
    color: var(--accent);
  }
  .divider {
    position: absolute; left: 40px; right: 40px; top: 178px;
    height: 1px; background: var(--accent);
  }
  .person {
    position: absolute; right: 40px; top: 128px; text-align: right;
  }
  .person__name {
    font-size: 20px; font-weight: 600; letter-spacing: 1.5px;
    color: var(--accent); text-transform: uppercase;
  }
  .person__title { font-size: 13px; color: var(--text); letter-spacing: 1px; margin-top: 2px; }
  .contact {
    position: absolute; left: 40px; top: 196px;
    list-style: none; font-size: 12.5px; color: var(--text);
  }
  .contact li { display: flex; align-items: center; gap: 9px; line-height: 22px; }
  .contact svg { width: 12px; height: 12px; fill: var(--accent); flex: none; }
  .address {
    position: absolute; right: 40px; top: 196px; text-align: right;
    font-size: 12.5px; line-height: 22px; color: var(--text);
  }
  /* back */
  .card--back .brand-name {
    left: 0; right: 0; top: 100px; text-align: center;
    font-size: 64px; color: var(--emboss);
  }
  .licences {
    position: absolute; left: 0; right: 0; bottom: 36px; text-align: center;
    font-size: 12.5px; letter-spacing: .8px; color: var(--muted);
  }
  .licences .dot { color: var(--accent); margin: 0 10px; }
</style>
</head>
<body>
<main class="sheet">
  <section class="card card--front">
    <div class="brand-name">HearthMile</div>
    <div class="person">
      <div class="person__name">Marcus Pell</div>
      <div class="person__title">CEO</div>
    </div>
    <div class="divider"></div>
    <ul class="contact">
      <li><svg viewBox="0 0 24 24"><path d="M6.6 10.8a15.1 15.1 0 0 0 6.6 6.6l2.2-2.2c.3-.3.7-.4 1-.2 1.1.4 2.3.6 3.6.6.6 0 1 .4 1 1V20c0 .6-.4 1-1 1C10.6 21 3 13.4 3 4c0-.6.4-1 1-1h3.5c.6 0 1 .4 1 1 0 1.3.2 2.5.6 3.6.1.3 0 .7-.2 1z"/></svg>732-555-0182</li>
      <li><svg viewBox="0 0 24 24"><path d="M2 5h20v14H2zm2 2v.4l8 5 8-5V7l-8 5z"/></svg>email@hearthmile.example</li>
      <li><svg viewBox="0 0 24 24"><path d="M12 2a10 10 0 1 0 0 20 10 10 0 0 0 0-20zm0 2c1 0 2.3 2 2.8 5H9.2C9.7 6 11 4 12 4zM4.3 11h3.8a19 19 0 0 0 0 2H4.3a8 8 0 0 1 0-2zm5.9 0h3.6a17 17 0 0 1 0 2h-3.6a17 17 0 0 1 0-2zm5.7 0h3.8a8 8 0 0 1 0 2h-3.8a19 19 0 0 0 0-2zM9.2 15h5.6c-.5 3-1.8 5-2.8 5s-2.3-2-2.8-5z"/></svg>www.hearthmile.example</li>
    </ul>
    <div class="address">48 Birchwell Court, Suite 314<br>Marlow Springs, NJ 07741</div>
    <div class="card__band"></div>
  </section>

  <section class="card card--back">
    <div class="brand-name">HearthMile</div>
    <p class="licences">NMLS 61947<span class="dot">•</span>Company NMLS 274615</p>
    <div class="card__band"></div>
  </section>
</main>
</body>
</html>
```